Dietitian needs awesome business card

I need a contemporary design that's eye catching but professional.
My card is to given to doctors, specialists and patients alike.
I manage patients with chronic diseases
I have uploaded my logo and current business card, I would also like the other Certified Clinical Nutritionist logo incorporated into the design

Target Market(s)

Doctors, specialists and patients

Industry/Entity Type

Healthcare

Contact Information for Business Card

www.brightfieldnutrition.com.au
Ph: 0427 561 903
Fax: 6457 2183
email: marcus.k.diet@fernmail.com
Space on the back of the card with: Appointment date, Appointment time and appointment location

Font styles to use
Serif

Colors
fbee3e
876aae
ffc214

Requirements
Must have
• My Logo
• Certified Clinical Nutritionist Logo
• My 4 locations - Pinebrook Medical Centre, North Corrin Health, Hollis Medical, Ashcombe Doctors Surgery
Nice to have
• I like the colours in my current business card

```html
<!DOCTYPE html>
<html lang="en">
<head>
<meta charset="utf-8">
<title>Brightfield Nutrition &amp; Dietetics – Business Card</title>
<link href="https://fonts.googleapis.com/css2?family=Open+Sans:wght@400;600;700&family=PT+Serif:wght@400;700&display=swap" rel="stylesheet">
<style>
  :root {
    --backdrop: #2b2b2d;
    --card-white: #ffffff;
    --badge-orange: #f26b1d;
    --label-blue: #2e4fa8;
    --rule-grey: #b9bcc4;
    --band-green: #5c6b4f;
    --band-text: #f4f1e6;
    --wave-blue-deep: #0f2f9c;
    --wave-blue-light: #2c6be0;
    --wave-green: #9cc820;
    --brand-navy: #1e2f8c;
    --brand-dot: #6cb33f;
  }
  * { box-sizing: border-box; margin: 0; padding: 0; }
  html, body { width: 1200px; height: 950px; overflow: hidden; }
  body {
    background: var(--backdrop);
    font-family: "Open Sans", Arial, sans-serif;
    position: relative;
  }
  .card {
    position: absolute;
    width: 540px;
    height: 330px;
    background: var(--card-white);
    border-radius: 4px;
    overflow: hidden;
    box-shadow: 0 10px 28px rgba(0,0,0,0.45);
  }

  /* ---------- Back of card ---------- */
  .card-back { left: 70px; top: 90px; }
  .credential-badge {
    position: absolute; left: 40px; top: 78px;
    width: 122px; height: 56px;
    background: var(--badge-orange);
    border-radius: 4px;
  }
  .appointment {
    position: absolute; left: 196px; top: 30px; right: 40px;
    color: var(--label-blue);
    font-size: 14px;
  }
  .appointment-row {
    display: flex; align-items: flex-end; gap: 6px;
    height: 24px;
  }
  .appointment-row .dots {
    flex: 1;
    border-bottom: 2px dotted var(--label-blue);
    margin-bottom: 4px;
  }
  .appointment-row .suffix { font-size: 9px; margin-bottom: 3px; }
  .writing-lines {
    position: absolute; left: 40px; right: 40px; top: 118px;
  }
  .writing-lines span {
    display: block; height: 30px;
    border-bottom: 1px solid var(--rule-grey);
  }
  .writing-lines span:first-child { margin-left: 156px; }
  .region-band {
    position: absolute; left: 0; right: 0; bottom: 0; height: 52px;
    background: linear-gradient(180deg, #66755a, var(--band-green));
    display: flex; align-items: center; justify-content: center;
    font-family: "PT Serif", Georgia, serif;
    color: var(--band-text);
    font-size: 19px; letter-spacing: 0.3px;
  }

  /* ---------- Front of card ---------- */
  .card-front { left: 590px; top: 520px; }
  .card-front .wave { position: absolute; inset: 0; }
  .contact {
    position: absolute; right: 26px; top: 22px;
    text-align: right; color: #fff;
  }
  .contact-name { font-size: 21px; font-weight: 700; line-height: 1.1; margin-right: 26px; }
  .contact-role { font-size: 12px; font-weight: 600; margin: 2px 26px 10px 0; }
  .contact-line {
    display: flex; justify-content: flex-end; align-items: center; gap: 8px;
    font-size: 12.5px; line-height: 20px;
  }
  .contact-line svg { width: 16px; height: 14px; flex: none; }
  .brand {
    position: absolute; left: 30px; bottom: 40px;
    display: flex; align-items: center; gap: 12px;
  }
  .brand-dot {
    width: 54px; height: 54px; border-radius: 50%;
    background: var(--brand-dot);
  }
  .brand-name {
    font-family: "PT Serif", Georgia, serif;
    font-size: 26px; font-weight: 400; color: var(--brand-navy);
    line-height: 1.05;
  }
</style>
</head>
<body>

<section class="card card-back" aria-label="Card back">
  <div class="credential-badge" role="img" aria-label="Certified Clinical Nutritionist badge"></div>
  <div class="appointment">
    <div class="appointment-row"><span>Date :</span><span class="dots"></span><span class="suffix">AM/PM</span></div>
    <div class="appointment-row"><span>Time :</span><span class="dots"></span></div>
  </div>
  <div class="writing-lines" aria-label="Appointment location lines">
    <span></span><span></span><span></span><span></span>
  </div>
  <div class="region-band">Dietitian for Corrin &amp; the North East Highlands</div>
</section>

<section class="card card-front" aria-label="Card front">
  <svg class="wave" viewBox="0 0 540 330" preserveAspectRatio="none" aria-hidden="true">
    <defs>
      <linearGradient id="waveBlue" x1="0" y1="0" x2="1" y2="1">
        <stop offset="0" stop-color="#0b2a92"/>
        <stop offset="0.55" stop-color="#1d55d0"/>
        <stop offset="1" stop-color="#0f2f9c"/>
      </linearGradient>
    </defs>
    <path d="M0,0 H540 V225 C450,192 380,172 250,162 C150,154 60,132 0,106 Z" fill="url(#waveBlue)"/>
    <path d="M0,114 C60,140 150,166 250,173 C380,182 450,202 540,234" fill="none" stroke="var(--wave-green)" stroke-width="4"/>
  </svg>

  <div class="contact">
    <div class="contact-name">Marcus Kendrick</div>
    <div class="contact-role">Nutritionist &amp; Chef</div>
    <div class="contact-line">0427 561 903
      <svg viewBox="0 0 16 14" aria-hidden="true"><path d="M2 4 Q8 0 14 4 L12 6 L10 4 H6 L4 6 Z M3 7 H13 V13 H3 Z" fill="#fff"/></svg>
    </div>
    <div class="contact-line">6457 2183
      <svg viewBox="0 0 16 14" aria-hidden="true"><rect x="4" y="1" width="8" height="4" fill="#fff"/><rect x="1" y="5" width="14" height="6" rx="1" fill="#fff"/><rect x="4" y="9" width="8" height="4" fill="#fff" stroke="#1d55d0" stroke-width="1"/></svg>
    </div>
    <div class="contact-line">marcus.k.diet@fernmail.com
      <svg viewBox="0 0 16 14" aria-hidden="true"><rect x="1" y="2" width="14" height="10" fill="#fff"/><path d="M1 2 L8 8 L15 2" fill="none" stroke="#1d55d0" stroke-width="1.2"/></svg>
    </div>
    <div class="contact-line">brightfieldnutrition.com.au
      <svg viewBox="0 0 16 14" aria-hidden="true"><circle cx="8" cy="7" r="6" fill="#fff"/><path d="M2 7 H14 M8 1 C5 4 5 10 8 13 M8 1 C11 4 11 10 8 13" fill="none" stroke="#1d55d0" stroke-width="1"/></svg>
    </div>
  </div>

  <div class="brand">
    <span class="brand-dot" aria-hidden="true"></span>
    <span class="brand-name">Brightfield Nutrition &amp; Dietetics</span>
  </div>
</section>

</body>
</html>
```